Create Premium Wine Label Design

We are premium wine exporters from Australia. We are looking to introduce new brand " The Velmora" - in red wine, White wine and Sparkling wine to international market.

The sample label design for red wine ( Shiraz) is attached.

This is our luxury brand. We need a stunning wine label designs for (front, back and neck) that should be mostly in GOLD colour and design should be really eye catching.

We have provided sample design for front, back and neck labels. However, we are looking forward to see a completely new improvised design.

LOGO attached.

Front Label Design Specification:

* We would like to see designs that are in Gold colour.
* Wine Bottle size is standard: 750ml; we assume the same design can be resizable to different bottle sizes.
* Our design should suit both black, white and sparkling wine bottles(sample attached)
* Use our logo in the design (see attached - label sample)
* Content for front label (see attached).
* Design should include all information specified in the sample

Back Label Design
* All contents in the sample should be used ( sample attached)
* LOGO attached.

Neck Label Design
* Sample of Neck label attached, please provide similar or your own design.
* LOGO attached.

Image Samples:
* Samples of label designs we like (see attached)
* Sample for gold color (see attached)
* For bottle shapes (see attached)
* Front, Back and Neck Label Samples (see attached)

Target Market(s)

International Wine Market

Font styles to use
Decorative
Script

Requirements
Must have
• Must have golden color on front and back label

```html
<!DOCTYPE html>
<html lang="en">
<head>
<meta charset="utf-8">
<title>The Velmora Shiraz – Front and Neck Labels</title>
<link rel="stylesheet" href="https://fonts.googleapis.com/css2?family=Cinzel:wght@500;700&family=Cinzel+Decorative:wght@700&family=Playfair+Display:wght@700&family=Fira+Sans:wght@700&display=swap">
<style>
  :root {
    --backdrop: #151515;
    --label-black: #070707;
    --gold: #d4b24c;
    --gold-light: #f0d77e;
    --gold-deep: #9c7a22;
    --ivory: #f2f0ea;
    --lace-light: #3c3c3c;
    --lace-mid: #2a2a2a;
    --lace-dark: #151515;
  }
  * { box-sizing: border-box; margin: 0; padding: 0; }
  html, body { width: 1200px; height: 1200px; overflow: hidden; }
  body {
    background: var(--backdrop);
    position: relative;
    font-family: "Cinzel", serif;
  }

  /* Front label */
  .front-label {
    position: absolute;
    left: 70px; top: 170px;
    width: 580px; height: 860px;
    background: var(--label-black);
  }
  .front-label .brand {
    position: absolute; left: 0; right: 0; top: 96px;
    display: flex; flex-direction: column; align-items: center;
  }
  .brand-row { display: flex; align-items: center; gap: 12px; }
  .brand-dot {
    width: 22px; height: 22px; border-radius: 50%;
    background: var(--gold);
  }
  .brand-name {
    font-family: "Cinzel", serif; font-weight: 700;
    color: var(--gold); font-size: 32px; letter-spacing: 1px; line-height: 1;
  }
  .rule {
    width: 290px; height: 2px; margin: 10px 0 8px;
    background: linear-gradient(90deg, transparent, var(--gold) 8%, var(--gold) 92%, transparent);
  }
  .flourish {
    width: 230px; height: 26px;
    background: radial-gradient(ellipse 50% 50% at 50% 50%, var(--gold-light) 0%, var(--gold) 35%, rgba(156,122,34,0.5) 70%, transparent 100%);
  }

  .lace-medallion {
    position: absolute; left: 35px; top: 225px;
    width: 510px; height: 510px; border-radius: 50%;
    background: radial-gradient(circle, var(--lace-mid) 0%, var(--lace-light) 40%, var(--lace-mid) 70%, var(--lace-dark) 88%, var(--label-black) 100%);
  }
  .medallion-text {
    position: absolute; left: 0; right: 0; top: 225px; height: 510px;
    display: flex; flex-direction: column; align-items: center; justify-content: center;
  }
  .varietal {
    font-family: "Fira Sans", sans-serif; font-weight: 700;
    color: var(--gold); font-size: 42px; line-height: 1; letter-spacing: 1px;
  }
  .wine-name {
    display: flex; align-items: center; margin: 18px 0 16px;
  }
  .wine-name .article {
    font-family: "Cinzel", serif; font-weight: 700;
    color: var(--gold); font-size: 16px; line-height: 16px;
    writing-mode: vertical-rl; transform: rotate(180deg);
    margin-right: 6px;
  }
  .wine-name .title {
    font-family: "Cinzel Decorative", serif; font-weight: 700;
    font-size: 76px; line-height: 1;
    background: linear-gradient(180deg, var(--gold-light), var(--gold) 55%, var(--gold-deep));
    -webkit-background-clip: text; background-clip: text; color: transparent;
  }
  .vintage {
    font-family: "Playfair Display", serif; font-weight: 700;
    color: var(--ivory); font-size: 52px; line-height: 1;
  }

  .origin-band {
    position: absolute; left: 0; right: 0; top: 762px;
    height: 66px;
    background: linear-gradient(90deg, var(--gold-deep), var(--gold-light) 30%, var(--gold) 55%, var(--gold-light) 80%, var(--gold-deep));
    display: flex; align-items: center; justify-content: center;
  }
  .origin-band span {
    font-family: "Cinzel", serif; font-weight: 700;
    color: var(--label-black); font-size: 24px; letter-spacing: 0.5px;
  }

  /* Neck label */
  .neck-label {
    position: absolute;
    left: 790px; top: 420px;
    width: 340px; height: 360px;
    background: var(--label-black);
    display: flex; flex-direction: column; align-items: center; justify-content: center;
    gap: 70px;
  }
  .neck-label .brand-name { font-size: 26px; }
  .neck-label .brand-dot { width: 18px; height: 18px; }
  .neck-label .flourish { width: 320px; height: 44px; }
</style>
</head>
<body>
  <section class="front-label">
    <div class="brand">
      <div class="brand-row">
        <span class="brand-dot"></span>
        <span class="brand-name">KESTRELVALE</span>
      </div>
      <div class="rule"></div>
      <div class="flourish" role="img" aria-label="Gold scrollwork ornament"></div>
    </div>

    <div class="lace-medallion" role="img" aria-label="Round grey floral lace pattern behind the wine name"></div>
    <div class="medallion-text">
      <p class="varietal">SHIRAZ</p>
      <h1 class="wine-name"><span class="article">THE</span><span class="title">VELMORA</span></h1>
      <p class="vintage">2018</p>
    </div>

    <div class="origin-band"><span>WINE OF AUSTRALIA</span></div>
  </section>

  <section class="neck-label">
    <div class="brand-row">
      <span class="brand-dot"></span>
      <span class="brand-name">KESTRELVALE</span>
    </div>
    <div class="flourish" role="img" aria-label="Double gold scrollwork ornament band"></div>
  </section>
</body>
</html>
```